Flowmark Engineering Business Card

our company has just rebranded and taken on a new logo design. We now need to update our business cards with the new logo. This is also an opportunity to reformat and modernize our look. We are an engineering company so the look needs to be formal and professional yet it should look modern. Have a look at our current card and the new card should have the same information.

Target Market(s)

Engineering firms, government, mining companies

Industry/Entity Type

Mechanical Engineering

Contact Information for Business Card

see example attached

Requirements
Must have
• look professional and modern
Should not have
• should not include the office locations 'Brisbane, Sydney and Kuala Lumpur'
• you will find this on the example but it should not be included in these versions. please remove from your submissions and resubmit

```html
<!DOCTYPE html>
<html lang="en">
<head>
<meta charset="utf-8">
<title>Flowmark Engineering Business Card</title>
<link rel="stylesheet" href="https://fonts.googleapis.com/css2?family=Open+Sans:wght@400;600;700&display=swap">
<style>
  :root {
    --backdrop: #e4e4e6;
    --card: #ffffff;
    --brand-blue: #33409a;
    --teal: #35c0cc;
    --rule-grey: #6d6f73;
    --text-grey: #5a5c60;
    --name-teal: #2fb4c2;
  }
  * { box-sizing: border-box; margin: 0; padding: 0; }
  html, body {
    width: 1200px; height: 902px; overflow: hidden;
    background: var(--backdrop);
    font-family: "Open Sans", Arial, sans-serif;
  }
  .canvas {
    position: relative; width: 1200px; height: 902px;
  }
  .card {
    position: absolute; left: 280px; width: 640px; height: 366px;
    background: var(--card);
    box-shadow: 0 6px 18px rgba(0,0,0,0.18);
    overflow: hidden;
  }
  .card--front { top: 50px; }
  .card--back { top: 486px; }

  .brand {
    display: flex; align-items: center; gap: 14px;
    color: var(--brand-blue);
  }
  .brand__dot {
    width: 54px; height: 54px; border-radius: 50%;
    border: 5px solid var(--brand-blue);
    flex: none;
  }
  .brand__name {
    font-weight: 700; font-size: 30px; line-height: 1.05;
    letter-spacing: 0.5px; text-transform: uppercase;
  }
  .brand__name span { display: block; font-size: 17px; letter-spacing: 6px; }

  .card--front .brand {
    position: absolute; left: 50%; top: 50%;
    transform: translate(-50%, -50%);
  }

  .card--back .brand {
    position: absolute; left: 44px; top: 70px;
  }
  .brand--small .brand__dot { width: 46px; height: 46px; border-width: 4px; }
  .brand--small .brand__name { font-size: 26px; }
  .brand--small .brand__name span { font-size: 15px; letter-spacing: 5px; }

  .holder {
    position: absolute; right: 40px; top: 118px; text-align: right;
  }
  .holder__name {
    color: var(--name-teal); font-weight: 700; font-size: 19px;
  }
  .holder__title {
    color: var(--text-grey); font-size: 17px; margin-top: 2px;
  }

  .contact {
    position: absolute; left: 40px; bottom: 92px;
    list-style: none; color: var(--text-grey); font-size: 13.5px; line-height: 1.6;
  }
  .contact li { display: flex; align-items: center; gap: 7px; }
  .contact svg { width: 12px; height: 12px; fill: var(--teal); flex: none; }
  .contact .no-icon { padding-left: 19px; }

  .footer-rule {
    position: absolute; left: 0; right: 0; bottom: 64px; height: 6px;
    background: var(--rule-grey);
  }
  .footer-band {
    position: absolute; left: 0; right: 0; bottom: 0; height: 64px;
    background: var(--teal);
    display: flex; align-items: center; padding-left: 250px;
    color: #fff; font-size: 16px; letter-spacing: 2px;
  }
  .footer-band b { font-weight: 700; }
</style>
</head>
<body>
<main class="canvas">
  <section class="card card--front" aria-label="Card front">
    <div class="brand">
      <div class="brand__dot"></div>
      <div class="brand__name">Flowmark<span>Engineering</span></div>
    </div>
  </section>

  <section class="card card--back" aria-label="Card back">
    <div class="brand brand--small">
      <div class="brand__dot"></div>
      <div class="brand__name">Flowmark<span>Engineering</span></div>
    </div>

    <div class="holder">
      <p class="holder__name">Dana Whitfield</p>
      <p class="holder__title">Owner</p>
    </div>

    <ul class="contact">
      <li>
        <svg viewBox="0 0 24 24" aria-hidden="true"><path d="M6.6 10.8a15.1 15.1 0 0 0 6.6 6.6l2.2-2.2a1 1 0 0 1 1-.25 11.4 11.4 0 0 0 3.6.57 1 1 0 0 1 1 1V20a1 1 0 0 1-1 1A17 17 0 0 1 3 4a1 1 0 0 1 1-1h3.5a1 1 0 0 1 1 1c0 1.25.2 2.45.57 3.57a1 1 0 0 1-.25 1z"/></svg>
        512.000.4417
      </li>
      <li>
        <svg viewBox="0 0 24 24" aria-hidden="true"><path d="M2 5h20v14H2z M3 6l9 7 9-7" /></svg>
        dana@flowmarkeng.com
      </li>
      <li class="no-icon">2210 Cedar Bend Rd Austin TX 78731</li>
    </ul>

    <div class="footer-rule"></div>
    <div class="footer-band">www.<b>Flowmark</b>.com</div>
  </section>
</main>
</body>
</html>
```